Business Card Re-Design/Update

We'd like to update out business cards. I've included our current "Style guide" which has the colour scheme of the organisation in it. I've also included the branding files with logos etc in them.

I've also included a copy of one of our existing cards so that you can see how ugly/dated they look. I'd like a fresh modern corporate look.

Target Market(s)

These are for our clients, potential clients, industry contacts - like all business cards

Contact Information for Business Card

Name
Position
Company Address - Level 1, 47 Fernby Street, Carlow Qld 4072
Direct Phone
mobile
Email
Website -www.korvalit.com.au
Logo

Colors

Designer to choose colors to be used in the design.

Requirements
Must have
• Main Logo
• Cards will need to be editable to be able to personalize them for each new employee.
Nice to have
• The MapOut, ShipWell, KeepSteady would be okay to have if they can be sensibly and professionally added to the look without detracting from the main imagery.
• Maybe they could go on the back of the card? will leave this to your creative discretion as to whether/where they fit.
Should not have
• Should not have decorative or script fonts

```html
<!DOCTYPE html>
<html lang="en">
<head>
<meta charset="utf-8">
<title>KorvalIT Business Card</title>
<link rel="stylesheet" href="https://fonts.googleapis.com/css2?family=Work+Sans:wght@400;500&display=swap">
<style>
  :root {
    --backdrop: #1f1f20;
    --card: #141414;
    --card-edge: #1b1b1b;
    --emboss: #2c2c2c;
    --foil: #cfcfcf;
    --foil-soft: #a9a9a9;
    --rule: #5a5a5a;
  }
  * { margin: 0; padding: 0; box-sizing: border-box; }
  html, body {
    width: 1200px; height: 900px; overflow: hidden;
    background: var(--backdrop);
    font-family: "Work Sans", sans-serif;
  }
  .stage {
    position: relative; width: 1200px; height: 900px;
    display: flex; flex-direction: column; align-items: center; justify-content: center; gap: 24px;
  }
  .card {
    position: relative; width: 720px; height: 410px;
    background: linear-gradient(160deg, var(--card-edge), var(--card));
    box-shadow: 0 6px 18px rgba(0,0,0,.45);
  }
  .brand {
    display: flex; align-items: center; gap: 14px;
    font-weight: 500; letter-spacing: -0.5px; white-space: nowrap;
  }
  .brand-mark { width: 30px; height: 30px; border: 4px solid currentColor; flex: none; }
  .card-front .brand {
    position: absolute; left: 50%; top: 50%; transform: translate(-50%, -50%);
    color: var(--foil); font-size: 58px;
  }
  .card-front .brand-mark { width: 40px; height: 40px; border-width: 5px; }
  .card-back .brand {
    position: absolute; left: 48px; top: 50%; transform: translateY(-50%);
    color: var(--emboss); font-size: 44px;
  }
  .divider {
    position: absolute; left: 350px; top: 40px; bottom: 40px;
    width: 2px; background: var(--rule);
  }
  .contact {
    position: absolute; left: 374px; top: 44px; right: 24px;
    color: var(--foil);
  }
  .contact-name { font-size: 27px; font-weight: 500; letter-spacing: 1.5px; }
  .contact-role { font-size: 14px; letter-spacing: 1px; color: var(--foil-soft); margin-bottom: 12px; }
  .contact-address { font-size: 15px; letter-spacing: 1px; line-height: 1.35; margin-bottom: 12px; }
  .contact-list { list-style: none; font-size: 16px; letter-spacing: 1px; }
  .contact-list li { display: flex; align-items: center; gap: 10px; line-height: 1.55; }
  .contact-list svg { width: 13px; height: 13px; fill: var(--foil-soft); flex: none; }
</style>
</head>
<body>
<main class="stage">
  <section class="card card-front">
    <div class="brand"><span class="brand-mark"></span>Tovandrel</div>
  </section>

  <section class="card card-back">
    <div class="brand"><span class="brand-mark"></span>KorvalIT</div>
    <div class="divider"></div>
    <div class="contact">
      <p class="contact-name">MAREN HOLT</p>
      <p class="contact-role">Business Development Manager</p>
      <p class="contact-address">Suite 8, 22 Ridgeway Lane,<br>Carlow QLD 4072</p>
      <ul class="contact-list">
        <li><svg viewBox="0 0 12 12"><path d="M3 0h6v12H3zM4 1.5v8h4v-8z"/></svg>+61 (0)400 555 218</li>
        <li><svg viewBox="0 0 12 12"><path d="M0 4q6-4 12 0v2H9V4.5H3V6H0zM2 7h8l1 4H1z"/></svg>+61 (0)7 3100 5541</li>
        <li><svg viewBox="0 0 12 12"><path d="M1 1l3-1 2 3-2 2q1 2 3 3l2-2 3 2-1 3Q3 11 1 1z"/></svg>+61 (0)7 3100 5500</li>
        <li><svg viewBox="0 0 12 12"><path d="M3 0h6v3H3zM0 4h12v5H9v3H3V9H0zM4 8v3h4V8z"/></svg>+61 (0)7 3100 5509</li>
        <li><svg viewBox="0 0 12 12"><path d="M0 2h12v8H0zM1 3l5 4 5-4v-.2H1z"/></svg>mholt@korvalit.com.au</li>
        <li><svg viewBox="0 0 12 12"><circle cx="6" cy="6" r="6"/></svg>www.korvalit.com.au</li>
      </ul>
    </div>
  </section>
</main>
</body>
</html>
```